IT Support Business needs a Flyer Designed

Have just had new logo and business cards made for new business called Byte Harbor, am now in need of a new flyer design. Byte Harbor will be providing home and small business it support.
Updates
Byte Harbor flyer design brief has been uploaded. The contest has also been changed to payment guaranteed.
If you need anymore information please feel free to contact myself.
Project Deadline Extended
Reason: I signed up early to take advantage of the artfolly 24 hour sale, and was a few days late in providing a design brief. Therefore I am extending the deadline by 2 days, to ensure it lasts for a good 2 weeks.
Have worked on and refined the Design Brief a bit more, hoping it makes it a bit clearer as to what I want on the flyer. If you have any questions please do not hesitate to ask.
I have refined the design brief overnight, after receiving some feedback, please refer to newly uploaded file for this morning. I am hoping it makes things clearer and easier.
Industry/Entity Type
Small Business

```html
<!DOCTYPE html>
<html lang="en">
<head>
<meta charset="utf-8">
<title>Byte Harbor – Computer Repair Flyer</title>
<link rel="stylesheet" href="https://fonts.googleapis.com/css2?family=Bitter:wght@400&family=Open+Sans:wght@400&display=swap">
<style>
  :root {
    --brand-red: #e8352a;
    --brand-blue: #1b6aa6;
    --ink: #2f2f2f;
    --paper: #ffffff;
    --photo-light: #f4f4f4;
    --photo-mid: #b9b9b9;
    --photo-dark: #6d6d6d;
  }
  * { box-sizing: border-box; margin: 0; padding: 0; }
  html, body { width: 1200px; height: 798px; overflow: hidden; background: var(--paper); }
  .flyer { position: relative; width: 1200px; height: 798px; background: var(--paper); overflow: hidden; font-family: "Open Sans", sans-serif; color: var(--ink); }

  .headline { position: absolute; left: 50px; top: 92px; font-family: "Bitter", serif; font-weight: 400; font-size: 38px; letter-spacing: 0.3px; color: var(--ink); }
  .headline .accent { color: var(--brand-red); }

  .brand { position: absolute; right: 60px; top: 88px; display: flex; align-items: center; gap: 12px; }
  .brand-dot { width: 26px; height: 26px; border-radius: 50%; background: var(--brand-red); }
  .brand-name { font-family: "Bitter", serif; font-weight: 400; font-size: 40px; color: var(--brand-blue); }

  .services { position: absolute; left: 30px; top: 168px; width: 1160px; display: grid; grid-template-columns: repeat(8, 1fr); list-style: none; }
  .service { display: flex; flex-direction: column; align-items: center; text-align: center; font-size: 16.5px; line-height: 20px; color: var(--ink); }
  .service svg { width: 70px; height: 70px; margin-bottom: 22px; fill: var(--brand-red); }

  .photo { position: absolute; left: 0; top: 367px; width: 1200px; height: 431px; background: linear-gradient(100deg, var(--photo-light) 0%, var(--photo-light) 30%, var(--photo-mid) 60%, var(--photo-dark) 100%); }

  .wave { position: absolute; left: 0; top: 0; width: 1200px; height: 798px; }
  .wave .red-band { fill: var(--brand-red); }
  .wave .blue-band { fill: var(--brand-blue); }

  .benefits { position: absolute; left: 100px; top: 582px; list-style: none; color: #fff; font-size: 22px; line-height: 34px; }
  .benefits li { position: relative; padding-left: 32px; margin-bottom: 10px; }
  .benefits li svg { position: absolute; left: 0; top: 7px; width: 16px; height: 22px; fill: #fff; }
</style>
</head>
<body>
<main class="flyer">
  <h1 class="headline"><span class="accent">Computer Repair</span> You Can Depend On</h1>

  <div class="brand">
    <span class="brand-dot"></span>
    <span class="brand-name">Byte Harbor</span>
  </div>

  <ul class="services">
    <li class="service">
      <svg viewBox="0 0 60 60"><rect x="8" y="10" width="44" height="30" rx="2"/><rect x="4" y="42" width="52" height="5" rx="2"/><rect x="12" y="14" width="36" height="22" fill="#fff"/><path d="M20 32 L36 16 L40 20 L24 36 Z"/></svg>
      Computer<br>Repair, Service,<br>Install And<br>Upgrade
    </li>
    <li class="service">
      <svg viewBox="0 0 60 60"><rect x="18" y="4" width="24" height="16" rx="2"/><rect x="29" y="20" width="2" height="12"/><rect x="10" y="30" width="40" height="2"/><rect x="10" y="30" width="2" height="10"/><rect x="48" y="30" width="2" height="10"/><rect x="29" y="30" width="2" height="10"/><circle cx="11" cy="48" r="8"/><circle cx="30" cy="48" r="8"/><circle cx="49" cy="48" r="8"/></svg>
      Setting Up<br>Secure<br>Networks
    </li>
    <li class="service">
      <svg viewBox="0 0 60 60"><path d="M8 8 h44 v40 h-44z M12 12 v32 h36 v-32z"/><rect x="16" y="16" width="28" height="24" fill="none" stroke="#e8352a" stroke-width="1.5"/><path d="M28 24 h5 v14 l8 2 v14 h-16 l-5 -10 h5z"/></svg>
      Setting up<br>New<br>Hardware
    </li>
    <li class="service">
      <svg viewBox="0 0 60 60"><rect x="2" y="8" width="6" height="6"/><rect x="10" y="8" width="6" height="6"/><rect x="18" y="8" width="6" height="6"/><rect x="26" y="8" width="6" height="6"/><rect x="34.5" y="8.5" width="5" height="5" fill="none" stroke="#e8352a"/><rect x="42.5" y="8.5" width="5" height="5" fill="none" stroke="#e8352a"/><rect x="50.5" y="8.5" width="5" height="5" fill="none" stroke="#e8352a"/><path d="M30 20 L30 46 L36 40 L41 50 L45 48 L40 38 L48 38 Z"/></svg>
      Software<br>Install And<br>Configuration
    </li>
    <li class="service">
      <svg viewBox="0 0 60 60"><path d="M30 14 a13 13 0 0 1 8 23 v6 h-16 v-6 a13 13 0 0 1 8 -23z"/><rect x="23" y="45" width="14" height="3"/><rect x="24" y="50" width="12" height="3"/><rect x="27" y="55" width="6" height="3"/><rect x="29" y="2" width="2" height="8"/><path d="M12 8 l6 6 -1.5 1.5 -6 -6z M48 8 l-6 6 1.5 1.5 6 -6z"/><rect x="4" y="26" width="8" height="2"/><rect x="48" y="26" width="8" height="2"/></svg>
      Software<br>Tricks, Tips<br>and Tutorials
    </li>
    <li class="service">
      <svg viewBox="0 0 60 60"><path d="M4 8 h34 v24 h-34z"/><path d="M6 10 L21 22 L36 10" fill="none" stroke="#fff" stroke-width="2"/><circle cx="38" cy="38" r="17" fill="none" stroke="#e8352a" stroke-width="5"/><circle cx="38" cy="38" r="6" fill="none" stroke="#e8352a" stroke-width="4"/><rect x="43" y="30" width="4" height="14"/></svg>
      Internet<br>and Email<br>Setup
    </li>
    <li class="service">
      <svg viewBox="0 0 60 60"><path d="M14 44 a10 10 0 0 1 0 -20 a14 14 0 0 1 27 -4 a11 11 0 0 1 5 24z" fill="none" stroke="#e8352a" stroke-width="3"/><path d="M30 30 h18 v-5 l8 8 -8 8 v-5 h-18z"/><path d="M30 40 h-16 v-5 l-8 8 8 8 v-5 h16z"/></svg>
      Data Backup<br>and Recovery
    </li>
    <li class="service">
      <svg viewBox="0 0 60 60"><path d="M12 30 a18 18 0 0 1 36 0" fill="none" stroke="#e8352a" stroke-width="4"/><rect x="8" y="26" width="8" height="14" rx="3"/><rect x="44" y="26" width="8" height="14" rx="3"/><path d="M48 40 q0 8 -12 8" fill="none" stroke="#e8352a" stroke-width="2"/><path d="M10 60 q0 -12 20 -12 q20 0 20 12z"/></svg>
      Onsite and<br>Remote<br>Support<br>Available
    </li>
  </ul>

  <div class="photo" role="img" aria-label="Black and white photograph of a hand typing on a computer keyboard"></div>

  <svg class="wave" viewBox="0 0 1200 798" aria-hidden="true">
    <path class="red-band" d="M0 444 C350 400 800 520 1200 785 L1200 798 L0 798 Z"/>
    <path class="blue-band" d="M0 470 C380 440 820 560 1200 794 L1200 798 L0 798 Z"/>
  </svg>

  <ul class="benefits">
    <li><svg viewBox="0 0 16 22"><path d="M1 0 L1 17 L5 13 L8 20 L11 19 L8 12 L14 12 Z"/></svg>$40 Per Hour Specific Job,<br>Or Am Happy To Bundle, Provide<br>Flexible Pricing For More Complex Tasks</li>
    <li><svg viewBox="0 0 16 22"><path d="M1 0 L1 17 L5 13 L8 20 L11 19 L8 12 L14 12 Z"/></svg>No Call Out Fee</li>
    <li><svg viewBox="0 0 16 22"><path d="M1 0 L1 17 L5 13 L8 20 L11 19 L8 12 L14 12 Z"/></svg>Friendly, Hassle Free, Independent Advice And Recommendations Given</li>
  </ul>
</main>
</body>
</html>
```